New Coffee Shop business card

We are opening our new coffee shop and are needing business cards to take with us on February 6th to Atlanta, Ga to a show.

We will be offering the following menu type items:

coffee
teas
espresso
frappes
smoothies

sandwiches
soups
salads
pastries
ice cream

Our shop is in a rural country-side area and we would like to convey that feel in our shop. In addition to the cafe we will also be selling gifts and furniture and other home decor. Much of this merchandise will be rescued, refurbished or repurposed which is also a core value of what we are all about.

We have a company logo we would like incorporated into the design.

We will also provide files that have the elements of the logo which may also be useful in the design of the card.

Since we are not open yet we need one slightly altered version of the card as well as the final product which states "Opening in the summer 2015"

Target Market(s)

moderate to slightly upscale and folksy.

Industry/Entity Type

Coffee Shop

Contact Information for Business Card

Fern Kettle Coffee
name
address
phone number
email

Card

Font styles to use
Sans Serif

Requirements
Must have
• Must include Logo
• Must include information on menu.
• Must include information on our merchandise sales as described inthe project description.
• Color scheme to complement the logo
Nice to have
• The following descriptions
• "We are also selling gifts, furniture, and other home decoration."
• "We rescue, refurbish, and repurpose old furniture so it can live again."

```html
<!DOCTYPE html>
<html lang="en">
<head>
<meta charset="utf-8">
<title>Fern Kettle Coffee – Business Cards</title>
<link rel="stylesheet" href="https://fonts.googleapis.com/css2?family=Jost:wght@400;500&display=swap">
<style>
  :root {
    --page-bg: #d9d9d9;
    --card-bg: #0e0c0c;
    --ink-white: #f2f0ee;
    --ink-red: #a3262a;
    --ink-grey: #8a8787;
    --ink-beige: #d8c8a6;
    --frame-red: #5a1a1c;
    --frame-grey: #6b6666;
    --cup-dark: #3a1214;
  }
  * { box-sizing: border-box; margin: 0; padding: 0; }
  html, body { width: 1200px; height: 900px; overflow: hidden; }
  body {
    background: var(--page-bg);
    font-family: "Jost", "Futura", sans-serif;
    position: relative;
  }

  .card {
    position: absolute;
    width: 520px;
    height: 296px;
    background: var(--card-bg);
    box-shadow: 0 6px 18px rgba(0,0,0,0.35);
    overflow: hidden;
  }
  .card--front   { left: 60px;  top: 60px; }
  .card--opening { left: 620px; top: 200px; }
  .card--final   { left: 330px; top: 550px; }

  /* word border running round each card */
  .edge {
    position: absolute;
    display: flex;
    justify-content: space-between;
    align-items: center;
    font-size: 14px;
    letter-spacing: 0.3px;
    white-space: nowrap;
  }
  .edge--top    { top: 8px;    left: 28px; right: 28px; }
  .edge--bottom { bottom: 8px; left: 28px; right: 28px; transform: rotate(180deg); }
  .edge--right  { right: 6px; top: 34px; bottom: 34px; writing-mode: vertical-rl; }
  .edge--left   { left: 6px;  top: 34px; bottom: 34px; writing-mode: vertical-rl; transform: rotate(180deg); }
  .w-coffee { color: var(--ink-red); }
  .w-gifts, .w-furniture { color: var(--ink-grey); }
  .w-decor { color: var(--ink-white); }
  .dot { color: var(--ink-grey); font-size: 10px; }

  /* front */
  .brand {
    position: absolute;
    left: 56px; top: 70px;
    width: 200px;
    text-align: center;
  }
  .brand-mark {
    width: 100px; height: 100px;
    margin: 0 auto 12px;
    border-radius: 50%;
    background: var(--ink-white);
  }
  .brand-name {
    color: var(--ink-white);
    font-size: 28px;
    font-weight: 400;
    line-height: 1.1;
  }
  .pitch {
    position: absolute;
    left: 290px; top: 78px;
    width: 200px;
    text-align: center;
    color: var(--ink-white);
    font-size: 16px;
    line-height: 1.3;
    letter-spacing: 0.3px;
  }
  .pitch-divider { display: block; margin: 6px auto 4px; }

  /* contact + menu */
  .contact {
    position: absolute;
    left: 70px; top: 54px;
    width: 230px;
    text-align: center;
  }
  .contact-phone { color: var(--ink-white); font-size: 22px; letter-spacing: 0.5px; }
  .contact-line  { color: var(--ink-red); font-size: 15px; line-height: 1.2; }

  .menu {
    position: absolute;
    left: 62px; top: 142px;
    width: 250px; height: 112px;
    border: 2px solid var(--frame-red);
    border-radius: 26px;
    outline: 1px solid var(--frame-grey);
    outline-offset: -7px;
    text-align: center;
    padding-top: 22px;
  }
  .menu-title { color: var(--ink-red); font-size: 12px; font-weight: 500; }
  .menu-items { color: var(--ink-beige); font-size: 12px; line-height: 1.25; }

  .cup-art {
    position: absolute;
    border-radius: 6px;
    background: radial-gradient(ellipse at 50% 70%, var(--cup-dark) 0%, rgba(58,18,20,0.5) 45%, rgba(14,12,12,0) 75%);
  }
  .card--opening .cup-art { left: 320px; top: 30px; width: 180px; height: 250px; }
  .card--final   .cup-art { left: 310px; top: 36px; width: 180px; height: 250px; }

  .announcement {
    position: absolute;
    left: 338px; top: 80px;
    color: var(--ink-white);
    font-size: 30px;
    line-height: 1.02;
    text-transform: uppercase;
    letter-spacing: 0.5px;
  }
</style>
</head>
<body>

  <!-- Front: brand and merchandise -->
  <section class="card card--front">
    <div class="edge edge--top"><span class="dot">•</span><span class="w-coffee">coffee</span><span class="dot">•</span><span class="w-gifts">gifts</span><span class="dot">•</span><span class="w-furniture">furniture</span><span class="dot">•</span><span class="w-decor">home decor</span><span class="dot">•</span><span class="w-coffee">coffee</span><span class="dot">•</span><span class="w-gifts">gifts</span><span class="dot">•</span><span class="w-furniture">furniture</span></div>
    <div class="edge edge--right"><span class="w-decor">home decor</span><span class="dot">•</span><span class="w-coffee">coffee</span><span class="dot">•</span><span class="w-gifts">gifts</span></div>
    <div class="edge edge--bottom"><span class="w-furniture">furniture</span><span class="dot">•</span><span class="w-decor">home decor</span><span class="dot">•</span><span class="w-coffee">coffee</span><span class="dot">•</span><span class="w-gifts">gifts</span><span class="dot">•</span><span class="w-furniture">furniture</span><span class="dot">•</span><span class="w-decor">home decor</span></div>
    <div class="edge edge--left"><span class="w-decor">home decor</span><span class="dot">•</span><span class="w-coffee">coffee</span><span class="dot">•</span><span class="w-gifts">gifts</span></div>

    <div class="brand">
      <div class="brand-mark"></div>
      <div class="brand-name">Fern Kettle Coffee</div>
    </div>

    <div class="pitch">
      <p>We are also selling gifts, furniture, and other home decoration.</p>
      <svg class="pitch-divider" width="40" height="10" viewBox="0 0 40 10" aria-hidden="true">
        <path d="M2 7 C10 -1, 18 11, 26 4 S36 2, 38 3" fill="none" stroke="#f2f0ee" stroke-width="2"/>
      </svg>
      <p>We rescue, refurbish, and repurpose old furniture so it can live again.</p>
    </div>
  </section>

  <!-- Back: pre-opening version -->
  <section class="card card--opening">
    <div class="edge edge--top"><span class="w-coffee">coffee</span><span class="dot">•</span><span class="w-gifts">gifts</span><span class="dot">•</span><span class="w-furniture">furniture</span><span class="dot">•</span><span class="w-decor">home decor</span><span class="dot">•</span><span class="w-coffee">coffee</span><span class="dot">•</span><span class="w-gifts">gifts</span><span class="dot">•</span><span class="w-furniture">furniture</span></div>
    <div class="edge edge--right"><span class="w-decor">home decor</span><span class="dot">•</span><span class="w-coffee">coffee</span><span class="dot">•</span><span class="w-gifts">gifts</span></div>
    <div class="edge edge--bottom"><span class="w-furniture">furniture</span><span class="dot">•</span><span class="w-decor">home decor</span><span class="dot">•</span><span class="w-coffee">coffee</span><span class="dot">•</span><span class="w-gifts">gifts</span><span class="dot">•</span><span class="w-furniture">furniture</span><span class="dot">•</span><span class="w-decor">home decor</span></div>
    <div class="edge edge--left"><span class="w-decor">home decor</span><span class="dot">•</span><span class="w-coffee">coffee</span><span class="dot">•</span><span class="w-gifts">gifts</span></div>

    <div class="cup-art" role="img" aria-label="Steaming coffee cup illustration with curling steam"></div>

    <div class="contact">
      <p class="contact-phone">1404 5 318 902</p>
      <p class="contact-line">18 Millbrook Rd Ste 140,</p>
      <p class="contact-line">Atlanta GA 30310</p>
      <p class="contact-line">info@fernkettle.com</p>
    </div>

    <div class="menu">
      <p class="menu-title">MENU:</p>
      <p class="menu-items">coffee&nbsp; teas&nbsp; espresso<br>frappes smoothies sandwiches<br>soups&nbsp;&nbsp; salads&nbsp; pastries<br>ice cream</p>
    </div>

    <p class="announcement">Opening<br>in the<br>summer<br>2015</p>
  </section>

  <!-- Back: final version -->
  <section class="card card--final">
    <div class="edge edge--top"><span class="w-coffee">coffee</span><span class="dot">•</span><span class="w-gifts">gifts</span><span class="dot">•</span><span class="w-furniture">furniture</span><span class="dot">•</span><span class="w-decor">home decor</span><span class="dot">•</span><span class="w-coffee">coffee</span><span class="dot">•</span><span class="w-gifts">gifts</span><span class="dot">•</span><span class="w-furniture">furniture</span></div>
    <div class="edge edge--right"><span class="w-decor">home decor</span><span class="dot">•</span><span class="w-coffee">coffee</span><span class="dot">•</span><span class="w-gifts">gifts</span></div>
    <div class="edge edge--bottom"><span class="w-furniture">furniture</span><span class="dot">•</span><span class="w-decor">home decor</span><span class="dot">•</span><span class="w-coffee">coffee</span><span class="dot">•</span><span class="w-gifts">gifts</span><span class="dot">•</span><span class="w-furniture">furniture</span><span class="dot">•</span><span class="w-decor">home decor</span></div>
    <div class="edge edge--left"><span class="w-decor">home decor</span><span class="dot">•</span><span class="w-coffee">coffee</span><span class="dot">•</span><span class="w-gifts">gifts</span></div>

    <div class="cup-art" role="img" aria-label="Steaming coffee cup illustration with curling steam"></div>

    <div class="contact">
      <p class="contact-phone">1404 5 318 902</p>
      <p class="contact-line">18 Millbrook Rd Ste 140,</p>
      <p class="contact-line">Atlanta GA 30310</p>
      <p class="contact-line">info@fernkettle.com</p>
    </div>

    <div class="menu">
      <p class="menu-title">MENU:</p>
      <p class="menu-items">coffee&nbsp; teas&nbsp; espresso<br>frappes smoothies sandwiches<br>soups&nbsp;&nbsp; salads&nbsp; pastries<br>ice cream</p>
    </div>
  </section>

</body>
</html>
```